I need a business card for my original fine art pieces

I would like a business card design including a logo design for a new business in the art world. I am based in the Hunter Valley NSW Australia. I am a contemporary figurative, encaustic and wildlife artist. I would like to be able to upload my email and mobile number to this as well. This design should be one that I can incorporate into banners and flyers etc. Id like to incorporate one of my own images or partial image into the background or somewhere below. My initials are RJ and I would like these used as a logo type. I would like the use of some colour and it to be bright and catchy. The final design should communicate artwork custom made and commissions available.

Overview: Original Fine Artworks for sale, online, art galleries etc, Custom made to order and by commission.

Target market is world wide audience and corporate world

My figurative work is painted using acrylics in a lot of natural ochre colours that reflect the Australian Outback, on canvas, linen, paper or board: My encaustic work is created in a contemporary abstract style using a blow torch and a made with a medium of 100% pure bees wax, Damar resin, mixed media and coloured pigments, applied to Birch board. My wildlife are created using coloured pencil and mixed media on a variety of paper types or board.

```html
<!DOCTYPE html>
<html lang="en">
<head>
<meta charset="utf-8">
<title>Rhea Jarvis – Business Card</title>
<link href="https://fonts.googleapis.com/css2?family=Cinzel:wght@500&family=Libre+Baskerville&family=Montserrat:wght@400;500&display=swap" rel="stylesheet">
<style>
  :root {
    --stage: #2a2a2a;
    --ink: #0b0b0b;
    --paper: #ffffff;
    --accent: #f04e23;
    --text-light: #f2f2f2;
    --text-dark: #1a1a1a;
  }
  * { box-sizing: border-box; margin: 0; padding: 0; }
  html, body { width: 1200px; height: 900px; overflow: hidden; }
  body {
    background: var(--stage);
    font-family: "Montserrat", Arial, sans-serif;
    position: relative;
  }
  .card {
    position: absolute;
    width: 540px;
    height: 310px;
    border-radius: 18px;
    overflow: hidden;
    box-shadow: 0 14px 30px rgba(0,0,0,.5);
  }
  .card--front { left: 70px; top: 90px; background: var(--ink); }
  .card--back { left: 590px; top: 500px; background: var(--paper); }

  .brand { display: flex; align-items: center; justify-content: center; gap: 12px; }
  .brand__mark {
    width: 40px; height: 40px; border-radius: 50%;
    border: 2.5px solid var(--accent);
  }
  .brand__name {
    font-family: "Cinzel", Georgia, serif;
    font-weight: 500;
    color: var(--accent);
    font-size: 30px;
    letter-spacing: 1px;
    line-height: 1;
  }
  .brand__tagline {
    text-align: center;
    font-size: 14px;
    letter-spacing: 3.2px;
    margin-top: 6px;
  }

  /* front */
  .front__content {
    position: absolute; inset: 0;
    display: flex; flex-direction: column; align-items: center; justify-content: center;
  }
  .front__content .brand__tagline { color: var(--text-light); }
  .front__blurb {
    margin-top: 10px;
    color: var(--text-light);
    text-align: center;
    font-size: 14px;
    line-height: 1.45;
  }

  /* back */
  .back__shape { position: absolute; inset: 0; }
  .back__brand { position: absolute; left: 0; width: 440px; top: 62px; }
  .back__brand .brand__name { font-size: 26px; }
  .back__brand .brand__mark { width: 34px; height: 34px; }
  .back__brand .brand__tagline { color: var(--text-dark); font-size: 12px; letter-spacing: 2.6px; font-weight: 500; }

  .person {
    position: absolute; right: 285px; top: 236px; text-align: right;
  }
  .person__name {
    font-family: "Libre Baskerville", Georgia, serif;
    color: var(--accent); font-size: 22px; line-height: 1.1;
  }
  .person__role { color: var(--text-light); font-size: 13px; margin-top: 2px; }

  .divider {
    position: absolute; left: 270px; top: 206px; width: 1.5px; height: 86px;
    background: var(--text-light);
  }
  .contact {
    position: absolute; left: 290px; top: 178px;
    list-style: none; color: var(--text-light);
    font-size: 13px; line-height: 21px;
  }
  .contact li { display: flex; align-items: center; gap: 8px; }
  .contact svg { width: 11px; height: 11px; flex: none; }
  .contact__plain { padding-left: 0; }
  .contact__highlight { color: var(--accent); }
</style>
</head>
<body>

  <section class="card card--front" aria-label="Business card front">
    <div class="front__content">
      <div class="brand">
        <span class="brand__mark"></span>
        <span class="brand__name">Rhea Jarvis</span>
      </div>
      <p class="brand__tagline">ORIGINAL FINE ARTWORKS</p>
      <p class="front__blurb">
        Original Fine Artworks for sale<br>
        online, art galleries etc<br>
        Custom made to order and by commission.
      </p>
    </div>
  </section>

  <section class="card card--back" aria-label="Business card back">
    <svg class="back__shape" viewBox="0 0 540 310" width="540" height="310" aria-hidden="true">
      <path d="M0,222 Q300,212 540,78 L540,310 L0,310 Z" fill="var(--ink)"/>
      <path d="M0,212 Q300,202 540,68" fill="none" stroke="var(--accent)" stroke-width="4"/>
    </svg>

    <div class="back__brand">
      <div class="brand">
        <span class="brand__mark"></span>
        <span class="brand__name">Rhea Jarvis</span>
      </div>
      <p class="brand__tagline">ORIGINAL FINE ARTWORKS</p>
    </div>

    <div class="person">
      <p class="person__name">Rhea Jarvis</p>
      <p class="person__role">Director</p>
    </div>

    <span class="divider"></span>

    <ul class="contact">
      <li class="contact__plain">Hunter Valley Australia</li>
      <li class="contact__plain">ABN 12 345 678 901</li>
      <li>
        <svg viewBox="0 0 12 12"><rect x="3" y="0.8" width="6" height="10.4" rx="1.2" fill="none" stroke="var(--accent)" stroke-width="1.4"/><circle cx="6" cy="9.3" r="0.7" fill="var(--accent)"/></svg>
        +61 400 123 456
      </li>
      <li>
        <svg viewBox="0 0 12 12"><rect x="0.8" y="2.2" width="10.4" height="7.6" fill="none" stroke="var(--accent)" stroke-width="1.4"/><path d="M1 2.6 L6 6.6 L11 2.6" fill="none" stroke="var(--accent)" stroke-width="1.3"/></svg>
        rhea@jarvisart.com
      </li>
      <li>
        <svg viewBox="0 0 12 12"><circle cx="6" cy="6" r="5.2" fill="var(--accent)"/><path d="M0.8 6 H11.2 M6 0.8 C3.5 3.5 3.5 8.5 6 11.2 M6 0.8 C8.5 3.5 8.5 8.5 6 11.2" fill="none" stroke="var(--ink)" stroke-width="0.9"/></svg>
        <span>www.<span class="contact__highlight">rheajarvis</span>.com</span>
      </li>
    </ul>
  </section>

</body>
</html>
```